Visit card

Industry/Entity Type

Health Care

Contact Information for Business Card

O VITALIS SYSTEMS
Odile Brevard - chef de Projet

Requirements
Must have
• 318 Gaston Lemaire Street 59710 LORVAL Tel: 33 (0) 327 481 605 Mobile: 06 42 19 37 64 Web: www.quorvexsystems.example Contact: o.brevard@o-vitalissystems.example
Should not have
• Respect for color

```html
<!DOCTYPE html>
<html lang="fr">
<head>
<meta charset="utf-8">
<title>O Vitalis Systems — carte de visite</title>
<link rel="stylesheet" href="https://fonts.googleapis.com/css2?family=Roboto:wght@400;500;700&display=swap">
<style>
  :root {
    --bg: #e9e6e2;
    --card-dark: #3e3e40;
    --card-light: #ffffff;
    --red: #e2232e;
    --ink: #3a3a3c;
    --faint-dark: #4a4a4c;
    --faint-light: #ececec;
  }
  * { margin: 0; padding: 0; box-sizing: border-box; }
  html, body { width: 1200px; height: 1021px; overflow: hidden; }
  body {
    background: var(--bg);
    font-family: "Roboto", Arial, sans-serif;
    position: relative;
  }
  .card {
    position: absolute;
    left: 220px;
    width: 760px;
    height: 434px;
    overflow: hidden;
    box-shadow: 0 6px 18px rgba(0,0,0,.18);
  }
  .card--back { top: 46px; background: var(--card-dark); }
  .card--front { top: 530px; background: var(--card-light); }

  .deco-circle { position: absolute; border-radius: 50%; }
  .card--back .deco-circle {
    width: 420px; height: 420px; left: -150px; top: -50px;
    background: var(--faint-dark);
  }
  .card--front .deco-circle {
    width: 400px; height: 400px; right: -110px; top: 150px;
    background: var(--faint-light);
  }

  .brand-name {
    font-weight: 700;
    letter-spacing: 2px;
    text-transform: uppercase;
    white-space: nowrap;
  }
  .card--back .brand-name {
    position: absolute; right: 70px; top: 170px;
    font-size: 44px; color: #ffffff; line-height: 1;
  }
  .website-line {
    position: absolute; right: 60px; bottom: 48px;
    font-size: 18px; letter-spacing: 2px; color: #e4e4e4;
  }
  .website-line .domain { color: var(--red); }

  .front-brand {
    position: absolute; left: 56px; top: 48px;
    display: flex; align-items: center; gap: 18px;
  }
  .front-brand .brand-mark {
    width: 70px; height: 70px; border-radius: 50%;
    background: var(--ink);
  }
  .front-brand .brand-name { font-size: 30px; color: var(--ink); }

  .person { position: absolute; left: 56px; top: 168px; }
  .person-name { font-size: 28px; font-weight: 700; color: var(--red); }
  .person-role { font-size: 19px; color: var(--ink); margin-top: 2px; }

  .contact-list {
    position: absolute; left: 56px; top: 262px;
    list-style: none; font-size: 19px; color: var(--ink);
  }
  .contact-list li { display: flex; align-items: center; gap: 10px; line-height: 27px; white-space: nowrap; }
  .contact-list svg { width: 16px; height: 16px; flex: none; fill: var(--red); }
</style>
</head>
<body>

<section class="card card--back" aria-label="Verso">
  <div class="deco-circle"></div>
  <div class="brand-name">O Vitalis Systems</div>
  <div class="website-line">www.<span class="domain">quorvexsystems</span>.example</div>
</section>

<section class="card card--front" aria-label="Recto">
  <div class="deco-circle"></div>
  <div class="front-brand">
    <div class="brand-mark"></div>
    <div class="brand-name">O Vitalis Systems</div>
  </div>

  <div class="person">
    <div class="person-name">Odile Brevard</div>
    <div class="person-role">chef de Projet</div>
  </div>

  <ul class="contact-list">
    <li>
      <svg viewBox="0 0 16 16"><path d="M3 1l3 3-1.5 2c1 2 3 4 5.5 5.5L12 10l3 3-2 2C7 15 1 9 1 3z"/></svg>
      +33 (0) 327 481 605
    </li>
    <li>
      <svg viewBox="0 0 16 16"><path d="M4 0h8a1 1 0 011 1v14a1 1 0 01-1 1H4a1 1 0 01-1-1V1a1 1 0 011-1zm1 2v10h6V2z"/></svg>
      06 42 19 37 64
    </li>
    <li>
      <svg viewBox="0 0 16 16"><path d="M0 3h16v10H0zm2 2v.5l6 4 6-4V5L8 9z"/></svg>
      o.brevard@o-vitalissystems.example
    </li>
    <li>
      <svg viewBox="0 0 16 16"><path d="M8 0a8 8 0 110 16A8 8 0 018 0zM2 7h3a12 12 0 011-5A6 6 0 002 7zm5 0h2a10 10 0 00-1-5 10 10 0 00-1 5zm4 0h3a6 6 0 00-4-5 12 12 0 011 5zM2 9a6 6 0 004 5 12 12 0 01-1-5zm5 0a10 10 0 001 5 10 10 0 001-5zm4 0a12 12 0 01-1 5 6 6 0 004-5z"/></svg>
      www.quorvexsystems.example
    </li>
    <li>
      <svg viewBox="0 0 16 16"><path d="M8 0a5.5 5.5 0 015.5 5.5C13.5 10 8 16 8 16S2.5 10 2.5 5.5A5.5 5.5 0 018 0zm0 3a2.5 2.5 0 100 5 2.5 2.5 0 000-5z"/></svg>
      318 Rue Gaston Lemaire, 59710 LORVAL
    </li>
  </ul>
</section>

</body>
</html>
```